New Business Card Design for Manufacturing

We are an engineering/manufacturing company that offers Advanced machining/assembly/engineering services, as well as innovative products for the heavy duty engine cooling markets.

We are looking to get a new business card designed that is clean and modern looking, but still fits the wide range of technical/skilled work we do.

- We hope to use this design as the base for other design work in new Presentations, web, and print work.

Industry/Entity Type

Engineering

Contact Information for Business Card

Our preferred color of blue is (RGB) 22/71/159 but can vary slightly from that color. Our content will be our Logo and full company name (Vantrell Forge Works, Inc.), company address, name, job title, phone number with extension, cell number, fax number, website, and email address on the cards.
We'd like the full company name next to the logo, but we are open to other interpretations of that layout.
Preferably, we would like the back side to be clean with just our logo, and the front to contain all of the contact information.

Colors
2f74b4
0355a3
85abd2

Requirements
Must have
• - Logo, company name, needed content - We are open to interpretation beyond that.
• - Standard size business card.
• - Horizontal orientation.
• - Enough space for lengthy names / job titles (for example, a job title could read "Directory of Human Resources" or "V.P. of Governmental Affairs"). We need this to look clean, whether the title be short (CEO) or long (as described above).

```html
<!DOCTYPE html>
<html lang="en">
<head>
<meta charset="utf-8">
<title>Vantrell Forge Works – Business Card</title>
<link href="https://fonts.googleapis.com/css2?family=Open+Sans:wght@400;600;800&display=swap" rel="stylesheet">
<style>
  :root {
    --backdrop: #3b3b3d;
    --card-black: #1d1d1f;
    --gloss: #2c2c2f;
    --brand-blue: #1f6fc4;
    --deep-blue: #0355a3;
    --light-blue: #2f9be0;
    --steel: #8b949c;
    --white: #ffffff;
  }
  * { margin: 0; padding: 0; box-sizing: border-box; }
  html, body { width: 799px; height: 1200px; overflow: hidden; }
  body {
    background: var(--backdrop);
    font-family: "Open Sans", Arial, sans-serif;
    position: relative;
  }
  .card {
    position: absolute;
    left: 50px;
    width: 700px;
    height: 400px;
    background: var(--card-black);
    overflow: hidden;
    box-shadow: 0 14px 30px rgba(0,0,0,.45);
  }
  .card-back { top: 110px; }
  .card-front { top: 660px; }

  .back-mark {
    position: absolute;
    inset: 0;
    display: flex;
    align-items: center;
    justify-content: center;
    gap: 18px;
  }
  .back-mark .mark-square {
    width: 34px; height: 34px;
    background: var(--gloss);
  }
  .back-mark .mark-name {
    font-weight: 800;
    font-size: 84px;
    letter-spacing: 2px;
    color: var(--gloss);
  }

  .front-art { position: absolute; inset: 0; }

  .holder { position: absolute; left: 40px; top: 34px; }
  .holder-name { color: var(--brand-blue); font-size: 25px; font-weight: 600; }
  .holder-title { color: var(--white); font-size: 13px; margin-top: 2px; }

  .front-mark {
    position: absolute;
    right: 40px;
    top: 110px;
    text-align: right;
  }
  .front-mark .mark-name {
    color: var(--brand-blue);
    font-weight: 800;
    font-size: 52px;
    letter-spacing: 1px;
    line-height: 1;
  }
  .front-mark .company-name {
    color: var(--brand-blue);
    font-size: 18px;
    margin-top: 10px;
  }

  .contact-list {
    position: absolute;
    left: 40px;
    top: 222px;
    list-style: none;
    color: var(--white);
    font-size: 15px;
    line-height: 24px;
  }
  .contact-list li { display: flex; align-items: center; gap: 10px; }
  .contact-list svg { width: 14px; height: 14px; fill: var(--white); flex: none; }

  .address {
    position: absolute;
    right: 40px;
    bottom: 26px;
    color: var(--white);
    font-size: 17px;
    line-height: 24px;
    text-align: right;
  }
</style>
</head>
<body>

<section class="card card-back" aria-label="Card back">
  <div class="back-mark">
    <span class="mark-square"></span>
    <span class="mark-name">VANTRELL</span>
  </div>
</section>

<section class="card card-front" aria-label="Card front">
  <svg class="front-art" viewBox="0 0 700 400" preserveAspectRatio="none" aria-hidden="true">
    <defs>
      <linearGradient id="waveBlue" x1="0" y1="0" x2="1" y2="1">
        <stop offset="0" stop-color="#1383d2"/>
        <stop offset="0.5" stop-color="#0b8ddc"/>
        <stop offset="1" stop-color="#0355a3"/>
      </linearGradient>
    </defs>
    <path d="M0,120 C170,95 270,175 370,232 S600,300 700,288" fill="none" stroke="var(--steel)" stroke-width="9"/>
    <path d="M0,140 C160,112 260,192 360,252 S600,322 700,308 L700,400 L0,400 Z" fill="url(#waveBlue)"/>
    <path d="M0,140 C160,112 260,192 360,252 S600,322 700,308" fill="none" stroke="#111113" stroke-width="6"/>
  </svg>

  <div class="holder">
    <div class="holder-name">Marcus Ellery Hale</div>
    <div class="holder-title">Managing Director</div>
  </div>

  <div class="front-mark">
    <div class="mark-name">VANTRELL</div>
    <div class="company-name">Vantrell Forge Works, Inc.</div>
  </div>

  <ul class="contact-list">
    <li><svg viewBox="0 0 16 16"><path d="M3 1h3l1 4-2 1a9 9 0 0 0 5 5l1-2 4 1v3c0 1-1 2-2 2A13 13 0 0 1 1 3c0-1 1-2 2-2z"/></svg>555-0142-2200 (VFW)</li>
    <li><svg viewBox="0 0 16 16"><path d="M4 1h8v4H4zM1 6h14v6h-3v3H4v-3H1zM5 10v4h6v-4z"/></svg>555-0178-3341</li>
    <li><svg viewBox="0 0 16 16"><path d="M5 0h6a1 1 0 0 1 1 1v14a1 1 0 0 1-1 1H5a1 1 0 0 1-1-1V1a1 1 0 0 1 1-1zm0 2v11h6V2z"/></svg>555-0193-4410</li>
    <li><svg viewBox="0 0 16 16"><path d="M0 3h16v10H0zm1 1v1l7 5 7-5V4z"/></svg>m.hale@vantrellforge.com</li>
    <li><svg viewBox="0 0 16 16"><path d="M8 0a8 8 0 1 0 0 16A8 8 0 0 0 8 0zm0 1.5c1 1 1.7 2.8 1.9 5H6.1C6.3 4.3 7 2.5 8 1.5zM1.6 7.5h3c.1 2 .6 3.8 1.5 5.1A6.5 6.5 0 0 1 1.6 7.5zm3-1h-3a6.5 6.5 0 0 1 4.5-5.1c-.9 1.3-1.4 3.1-1.5 5.1zm1.5 1h3.8c-.2 2.2-.9 4-1.9 5-1-1-1.7-2.8-1.9-5zm5.3 0h3a6.5 6.5 0 0 1-4.5 5.1c.9-1.3 1.4-3.1 1.5-5.1zm0-1c-.1-2-.6-3.8-1.5-5.1a6.5 6.5 0 0 1 4.5 5.1z"/></svg>www.vantrellforge.com</li>
  </ul>

  <div class="address">87 Foundry Lane,<br>Millbrook, OH 44012</div>
</section>

</body>
</html>
```